Year 12 Chemistry Workbook illustrations and diagrams

We are producing a Chemistry Workbook for senior high-school students in South Australia and require a designer to create illustrations including detailed diagrams and graphs for our upcoming publication.

The attached files are illustrations that we'd like to have recreated, with your own personal style incorporated.

We will require you to do the following:
- Create vector artwork
- Supply AI files
- Use the font helvetica neue 45 light, or its italic variation
- Use full colour wherever possible
- Please use 100% black, not RGB black/eye-dropped black

Target Market(s)

Senior high school students

Industry/Entity Type

School

Font styles to use
Sans Serif

Colors

Designer to choose colors to be used in the design.

Requirements
Must have
• - Create vector artwork
• - Supply AI files
• - Use the font helvetica neue 45 light, or its italic variation
• - Use full colour wherever possible
• - Please use 100% black, not RGB black/eye-dropped black
Should not have
• Please do not use RGB black/eye-dropped black

```html
<!DOCTYPE html>
<html lang="en">
<head>
<meta charset="utf-8">
<title>Biodiesel production flowchart</title>
<link rel="stylesheet" href="https://fonts.googleapis.com/css2?family=Arimo:wght@400;700&display=swap">
<style>
  :root {
    --paper: #ffffff;
    --ink: #000000;
    --reactor: #f98012;
    --stirrer: #1d5b78;
    --unit-light: #8fe6f8;
    --unit-mid: #4ccbf0;
    --flow: #c64cf4;
    --product: #f98012;
    --unit-text: #ffffff;
  }
  html, body {
    margin: 0;
    padding: 0;
    width: 1200px;
    height: 849px;
    overflow: hidden;
    background: var(--paper);
  }
  .flowchart {
    display: block;
    width: 1200px;
    height: 849px;
    font-family: "Arimo", Arial, sans-serif;
  }
  .label { fill: var(--ink); font-size: 15.5px; }
  .heading { fill: var(--ink); font-size: 15.5px; }
  .unit-name { fill: var(--unit-text); font-size: 15px; }
  .product-name { fill: var(--product); font-size: 19px; font-weight: 700; }
  .vessel-reactor { fill: var(--reactor); }
  .unit-light { fill: var(--unit-light); }
  .unit-mid { fill: var(--unit-mid); }
  .stirrer-shaft { stroke: var(--stirrer); stroke-width: 8; stroke-linecap: round; }
  .stirrer-blade { fill: var(--stirrer); }
  .flow-line { fill: none; stroke: var(--flow); stroke-width: 7; stroke-linejoin: miter; }
  .flow-head { fill: var(--flow); }
</style>
</head>
<body>
<svg class="flowchart" viewBox="0 0 850 601" xmlns="http://www.w3.org/2000/svg">
  <defs>
    <marker id="arrowhead" viewBox="0 0 10 10" refX="2" refY="5" markerWidth="16" markerHeight="18" markerUnits="userSpaceOnUse" orient="auto">
      <path class="flow-head" d="M0,0 L10,5 L0,10 Z"/>
    </marker>
  </defs>

  <text class="heading" x="48" y="40">4.1.2&#160;&#160;&#160;Biodiesel can be produced according to the following industrial flowchart</text>

  <!-- Reactor -->
  <rect class="vessel-reactor" x="80" y="140" width="113" height="223" rx="9"/>
  <line class="stirrer-shaft" x1="127" y1="104" x2="127" y2="236"/>
  <ellipse class="stirrer-blade" cx="110" cy="240" rx="20" ry="12"/>
  <ellipse class="stirrer-blade" cx="146" cy="240" rx="20" ry="12"/>
  <text class="unit-name" transform="translate(174,157) rotate(90)">Transesterification</text>

  <text class="label" x="38" y="195">Oil</text>
  <path class="flow-line" d="M38,206 H64" marker-end="url(#arrowhead)"/>
  <text class="label" x="15" y="256">Alcohol +</text>
  <text class="label" x="15" y="279">Catalyst</text>
  <path class="flow-line" d="M38,292 H64" marker-end="url(#arrowhead)"/>
  <path class="flow-line" d="M201,206 H228" marker-end="url(#arrowhead)"/>

  <!-- Ester tank -->
  <rect class="vessel-reactor" x="244" y="145" width="95" height="166" rx="9"/>
  <text class="unit-name" x="254" y="168">Mixed</text>
  <text class="unit-name" x="254" y="190">ethyl</text>
  <text class="unit-name" x="254" y="212">esters</text>
  <path class="flow-line" d="M358,206 H392" marker-end="url(#arrowhead)"/>

  <!-- Ester line -->
  <rect class="unit-light" x="413" y="145" width="58" height="121" rx="9"/>
  <text class="unit-name" transform="translate(436,170) rotate(90)">Separator</text>
  <text class="label" x="419" y="90">Alcohol</text>
  <path class="flow-line" d="M441,131 V110" marker-end="url(#arrowhead)"/>
  <path class="flow-line" d="M478,206 H503" marker-end="url(#arrowhead)"/>

  <rect class="unit-light" x="519" y="145" width="58" height="121" rx="9"/>
  <text class="unit-name" transform="translate(552,150) rotate(90)">Extraction using</text>
  <text class="unit-name" transform="translate(534,170) rotate(90)">water</text>
  <text class="label" x="531" y="90">Water</text>
  <path class="flow-line" d="M547,100 V121" marker-end="url(#arrowhead)"/>
  <path class="flow-line" d="M547,274 V302 H577" marker-end="url(#arrowhead)"/>
  <text class="label" x="600" y="308">Wash water</text>
  <path class="flow-line" d="M585,206 H610" marker-end="url(#arrowhead)"/>

  <rect class="unit-light" x="625" y="145" width="60" height="121" rx="9"/>
  <text class="unit-name" transform="translate(648,170) rotate(90)">Separator</text>
  <text class="label" x="630" y="90">Water</text>
  <path class="flow-line" d="M654,131 V110" marker-end="url(#arrowhead)"/>
  <text class="label" x="734" y="167">Heat and</text>
  <text class="label" x="738" y="190">vacuum</text>
  <path class="flow-line" d="M726,168 H701" marker-end="url(#arrowhead)"/>
  <path class="flow-line" d="M692,237 H717" marker-end="url(#arrowhead)"/>
  <text class="product-name" x="730" y="244">Biodiesel</text>

  <!-- Glycerol line -->
  <text class="label" x="255" y="343">Crude</text>
  <text class="label" x="249" y="366">glycerol</text>
  <path class="flow-line" d="M313,316 V380 H346" marker-end="url(#arrowhead)"/>

  <rect class="unit-mid" x="375" y="348" width="59" height="120" rx="9"/>
  <text class="unit-name" transform="translate(398,373) rotate(90)">Separator</text>
  <text class="label" x="380" y="298">Alcohol</text>
  <path class="flow-line" d="M404,340 V318" marker-end="url(#arrowhead)"/>
  <text class="label" x="254" y="439">Heat and</text>
  <text class="label" x="258" y="462">vacuum</text>
  <path class="flow-line" d="M322,438 H349" marker-end="url(#arrowhead)"/>
  <path class="flow-line" d="M414,482 V497 H489" marker-end="url(#arrowhead)"/>

  <rect class="unit-mid" x="515" y="440" width="59" height="119" rx="9"/>
  <text class="unit-name" transform="translate(539,462) rotate(90)">Water wash</text>
  <text class="label" x="522" y="385">Water</text>
  <path class="flow-line" d="M544,398 V422" marker-end="url(#arrowhead)"/>

  <rect class="unit-mid" x="622" y="440" width="59" height="119" rx="9"/>
  <text class="unit-name" transform="translate(645,462) rotate(90)">Neutralizer</text>
  <text class="label" x="710" y="407">Acid</text>
  <path class="flow-line" d="M700,401 H647 V420" marker-end="url(#arrowhead)"/>
  <path class="flow-line" d="M688,497 H713" marker-end="url(#arrowhead)"/>
  <text class="label" x="685" y="525">Neutralized</text>
  <text class="label" x="699" y="548">glycerol</text>
</svg>
</body>
</html>
```